Construction company business card

One side to be the logo with the company name, The other side I would like: (Tomas verbick) Project manager 41 barrow crescent hallam 52917306224783(03) 9703 2428Info@gudeljgroup.comAnd then maybe a couple dot points saying what we do:Construction (commercial & industrial) Civil construction

Anything else please contact me!
Maybe curved st one edge of the card

Target Market(s)

Older clientele

Industry/Entity Type

Construction Company

Contact Information for Business Card

Read above

Colors
3277b5
1b1b1b
9d9d9d

Requirements
Must have
• Use my logo on one side
Nice to have
• Read above
Should not have
• Read above

```html
<!DOCTYPE html>
<html lang="en">
<head>
<meta charset="utf-8">
<title>Barrowline Construction – Business Card</title>
<link href="https://fonts.googleapis.com/css2?family=Work+Sans:wght@400;500;600&display=swap" rel="stylesheet">
<style>
  :root {
    --brand-blue: #3277b5;
    --card-black: #1b1b1b;
    --grey: #9d9d9d;
    --white: #ffffff;
    --backdrop: #3a3532;
  }
  * { margin: 0; padding: 0; box-sizing: border-box; }
  html, body { width: 1200px; height: 716px; overflow: hidden; }
  body {
    background: var(--backdrop);
    font-family: "Work Sans", Arial, sans-serif;
    position: relative;
  }
  .card {
    position: absolute;
    top: 213px;
    width: 520px;
    height: 289px;
    background: var(--card-black);
    border-radius: 6px;
    overflow: hidden;
    box-shadow: 0 12px 30px rgba(0,0,0,0.45);
  }
  .card--front { left: 50px; }
  .card--back { left: 630px; }

  /* Front */
  .brand {
    position: absolute;
    left: 0; right: 0; top: 78px;
    text-align: center;
    color: var(--white);
    font-weight: 600;
  }
  .brand__dot {
    display: block;
    width: 54px; height: 54px;
    margin: 0 auto 14px;
    border-radius: 50%;
    background: var(--brand-blue);
  }
  .brand__name { font-size: 30px; letter-spacing: 1px; text-transform: uppercase; line-height: 1; }
  .brand__sub { font-size: 12px; letter-spacing: 6px; text-transform: uppercase; margin-top: 6px; }

  /* Back */
  .card__waves { position: absolute; inset: 0; }
  .brand--small { top: 38px; left: 80px; right: auto; text-align: left; }
  .brand--small .brand__dot { width: 40px; height: 40px; margin: 0 0 10px 70px; }
  .brand--small .brand__name { font-size: 22px; }
  .brand--small .brand__sub { font-size: 9px; letter-spacing: 4.6px; margin-top: 4px; }

  .person {
    position: absolute;
    right: 30px; top: 112px;
    text-align: right;
  }
  .person__name {
    color: var(--brand-blue);
    font-size: 17px;
    font-weight: 500;
    text-transform: uppercase;
    letter-spacing: 0.5px;
  }
  .person__role { color: var(--white); font-size: 12px; margin-top: 3px; letter-spacing: 0.5px; }

  .contact {
    position: absolute;
    right: 30px; bottom: 14px;
    list-style: none;
    color: var(--white);
    font-size: 12px;
    line-height: 14px;
    text-align: right;
  }
  .contact li { display: flex; justify-content: flex-end; align-items: center; gap: 6px; }
  .contact svg { width: 9px; height: 9px; fill: var(--white); flex: none; }
  .contact .no-icon { padding-right: 15px; }
</style>
</head>
<body>

  <section class="card card--front" aria-label="Card front">
    <div class="brand">
      <span class="brand__dot"></span>
      <div class="brand__name">Barrowline</div>
      <div class="brand__sub">Construction</div>
    </div>
  </section>

  <section class="card card--back" aria-label="Card back">
    <svg class="card__waves" viewBox="0 0 520 289" preserveAspectRatio="none" aria-hidden="true">
      <path d="M0,95 C20,170 120,215 300,228 C150,225 40,200 0,150 Z" fill="var(--white)"/>
      <path d="M90,135 C135,182 225,200 330,200 C420,200 480,190 520,176" fill="none" stroke="var(--brand-blue)" stroke-width="5"/>
      <path d="M0,165 C60,235 200,245 300,232 C400,220 470,200 520,192 L520,289 L0,289 Z" fill="var(--brand-blue)"/>
    </svg>

    <div class="brand brand--small">
      <span class="brand__dot"></span>
      <div class="brand__name">Barrowline</div>
      <div class="brand__sub">Construction</div>
    </div>

    <div class="person">
      <div class="person__name">Tomas Verbick</div>
      <div class="person__role">Project manager</div>
    </div>

    <ul class="contact">
      <li class="no-icon">41 barrow crescent</li>
      <li class="no-icon">kessford 5291</li>
      <li>73 0622 4783
        <svg viewBox="0 0 10 10"><path d="M2,0.5 L3.6,0.5 L4.2,3 L3,3.8 C3.6,5 4.9,6.4 6.2,7 L7,5.8 L9.5,6.4 L9.5,8 C9.5,9 8.8,9.5 8,9.5 C4,9.2 0.8,6 0.5,2 C0.5,1.2 1,0.5 2,0.5 Z"/></svg>
      </li>
      <li>03 9418 6573
        <svg viewBox="0 0 10 10"><path d="M2.5,0 H7.5 V10 H2.5 Z M3.4,1 V8 H6.6 V1 Z"/></svg>
      </li>
      <li>Info@verbickgroup.com
        <svg viewBox="0 0 10 10"><path d="M0,2 H10 V8.5 H0 Z M1,3 V7.5 H9 V3 L5,5.8 Z M1.6,3 L5,5.2 L8.4,3 Z"/></svg>
      </li>
    </ul>
  </section>

</body>
</html>
```